Velmarotix - world unique technology for better life - please let them know who am i at first sight

We need a new business card for company which is a provider of unique crystal based technology suitable for all living being. For more information and final design you can use our brochure (our colours are black and blue from brochure).
We use Verdana font

Industry/Entity Type

Business

Contact Information for Business Card

regular dimension

Font styles to use
Other font styles liked:
• Verdana

Requirements
Must have
• Logo
• name
• function/position
• phone
• mobile
• e-mail
• adress
Nice to have
• inovative design (technology directed)

```html
<!DOCTYPE html>
<html lang="en">
<head>
<meta charset="utf-8">
<title>Velmarotix – Business Card</title>
<link rel="stylesheet" href="https://fonts.googleapis.com/css2?family=Open+Sans:wght@300;400&display=swap">
<style>
  :root {
    --stage: #e9e9e7;
    --card-white: #ffffff;
    --ink-black: #050505;
    --brand-blue: #14b4e4;
    --brand-blue-deep: #0aa3d6;
    --pattern-blue: #cfe4f2;
    --text-light: #ffffff;
    --shadow: rgba(0, 0, 0, 0.18);
  }
  html, body {
    margin: 0;
    padding: 0;
    width: 1200px;
    height: 858px;
    overflow: hidden;
    background: var(--stage);
    font-family: "Open Sans", Verdana, sans-serif;
  }
  .stage {
    position: relative;
    width: 1200px;
    height: 858px;
  }
  .card {
    position: absolute;
    top: 261px;
    width: 520px;
    height: 336px;
    background: var(--card-white);
    box-shadow: 0 10px 28px var(--shadow);
    overflow: hidden;
  }
  .card--contact { left: 60px; }
  .card--brand { left: 620px; }

  .card__panels {
    position: absolute;
    inset: 0;
    width: 100%;
    height: 100%;
  }

  /* Wordmark */
  .wordmark {
    position: absolute;
    display: flex;
    align-items: center;
    gap: 12px;
    color: var(--brand-blue);
  }
  .wordmark__dot {
    border-radius: 50%;
    background: var(--brand-blue);
    flex: none;
  }
  .wordmark__name {
    font-weight: 300;
    text-transform: uppercase;
    letter-spacing: 0.04em;
    line-height: 1;
  }
  .card--contact .wordmark { left: 26px; top: 214px; }
  .card--contact .wordmark__dot { width: 34px; height: 34px; }
  .card--contact .wordmark__name { font-size: 23px; }

  .card--brand .wordmark { left: 96px; top: 146px; }
  .card--brand .wordmark__dot { width: 52px; height: 52px; }
  .card--brand .wordmark__name { font-size: 34px; }

  /* Identity */
  .identity {
    position: absolute;
    right: 48px;
    top: 48px;
    text-align: right;
    color: var(--text-light);
  }
  .identity__name {
    font-size: 24px;
    font-weight: 300;
    line-height: 1.1;
    margin: 0;
  }
  .identity__role {
    font-size: 12px;
    font-weight: 400;
    margin: 4px 0 0;
  }

  /* Contact list */
  .contact {
    position: absolute;
    right: 26px;
    top: 170px;
    margin: 0;
    padding: 0;
    list-style: none;
    color: var(--text-light);
    font-size: 13px;
    font-weight: 300;
    line-height: 19px;
    text-align: right;
  }
  .contact__item {
    display: flex;
    justify-content: flex-end;
    align-items: center;
    gap: 10px;
  }
  .contact__icon {
    width: 11px;
    height: 11px;
    flex: none;
    fill: none;
    stroke: var(--text-light);
    stroke-width: 1.4;
  }
  .contact__address { padding-right: 21px; }

  .decor {
    position: absolute;
    border-radius: 50%;
    background: radial-gradient(circle, var(--pattern-blue) 0%, rgba(207,228,242,0.35) 60%, rgba(207,228,242,0) 72%);
  }
  .decor--top { width: 200px; height: 200px; left: -40px; top: -70px; }
  .decor--bottom { width: 300px; height: 300px; right: -60px; bottom: -150px; }
</style>
</head>
<body>
<main class="stage">

  <section class="card card--contact" aria-label="Business card, contact side">
    <svg class="card__panels" viewBox="0 0 520 336" preserveAspectRatio="none" aria-hidden="true">
      <defs>
        <linearGradient id="blueFade" x1="0" y1="0" x2="1" y2="1">
          <stop offset="0" stop-color="#1ec3ee"/>
          <stop offset="1" stop-color="#0a9fd2"/>
        </linearGradient>
      </defs>
      <rect class="panel-black" x="0" y="0" width="520" height="152" fill="#050505"/>
      <rect class="panel-blue" x="0" y="150" width="520" height="186" fill="url(#blueFade)"/>
      <polygon class="panel-white" points="0,0 200,0 288,152 208,336 0,336" fill="#ffffff"/>
    </svg>

    <div class="identity">
      <p class="identity__name">Your Name</p>
      <p class="identity__role">Position</p>
    </div>

    <ul class="contact">
      <li class="contact__item">000-0000-0000
        <svg class="contact__icon" viewBox="0 0 12 12"><rect x="3" y="1" width="6" height="10" rx="1"/></svg>
      </li>
      <li class="contact__item">+385(0) 41 772 903
        <svg class="contact__icon" viewBox="0 0 12 12"><path d="M3 1 L5 3.5 L4 5 Q5.5 7.5 7 8 L8.5 7 L11 9 L9.5 11 Q4 10 1 3 Z"/></svg>
      </li>
      <li class="contact__item">info@velmarotix.eu
        <svg class="contact__icon" viewBox="0 0 12 12"><rect x="1" y="2.5" width="10" height="7"/><path d="M1 2.5 L6 6.5 L11 2.5"/></svg>
      </li>
      <li class="contact__item">www.velmarotix.eu
        <svg class="contact__icon" viewBox="0 0 12 12"><circle cx="6" cy="6" r="5"/><path d="M1 6 H11 M6 1 Q9 6 6 11 Q3 6 6 1"/></svg>
      </li>
      <li class="contact__item">28-34 Harrow Lane London
        <svg class="contact__icon" viewBox="0 0 12 12"><path d="M6 11 Q2 6.5 2 4.5 A4 4 0 0 1 10 4.5 Q10 6.5 6 11 Z"/><circle cx="6" cy="4.5" r="1.3"/></svg>
      </li>
      <li class="contact__item contact__address">N7 2QB United Kingdom</li>
    </ul>

    <div class="wordmark">
      <span class="wordmark__dot" aria-hidden="true"></span>
      <span class="wordmark__name">Velmarotix</span>
    </div>
  </section>

  <section class="card card--brand" aria-label="Business card, brand side">
    <div class="decor decor--top" role="img" aria-label="Faint pale-blue crystal lattice decoration"></div>
    <div class="decor decor--bottom" role="img" aria-label="Faint pale-blue crystal lattice decoration"></div>

    <div class="wordmark">
      <span class="wordmark__dot" aria-hidden="true"></span>
      <span class="wordmark__name">Velmarotix</span>
    </div>
  </section>

</main>
</body>
</html>
```